Quillmoor Air Business Card Design

Design new, 2 sides, business cards for a residential and light commercial heating, air conditioning contractor.

Target Market(s)

Homeowners, small businesses

Industry/Entity Type

Business

Contact Information for Business Card

Dominic Westerhall
Phone - 862-415-2736
Email
Address - PO box 518
Brightwater NJ 07912
Website - www.QuillmoorAirLLC.example

Requirements
Must have
• logo, company colors, standard size with no die cut, so I can use nova stamp

```html
<!DOCTYPE html>
<html lang="en">
<head>
<meta charset="utf-8">
<title>Quillmoor Air Business Card</title>
<link href="https://fonts.googleapis.com/css2?family=Roboto:wght@400;500;700&family=Roboto+Slab:wght@700&display=swap" rel="stylesheet">
<style>
  :root {
    --backdrop: #e6e6e6;
    --ink-black: #0a0a0c;
    --maroon: #862a2c;
    --maroon-deep: #7a2326;
    --gold: #f5b400;
    --cream: #f6d98a;
    --orange: #e08a1c;
    --wave-yellow: #f1dc7c;
    --wave-red: #c8321f;
    --white: #ffffff;
  }
  * { margin: 0; padding: 0; box-sizing: border-box; }
  html, body { width: 1200px; height: 576px; overflow: hidden; }
  body {
    background: var(--backdrop);
    font-family: "Roboto", Arial, sans-serif;
    position: relative;
  }
  .card {
    position: absolute;
    top: 138px;
    width: 485px;
    height: 294px;
    overflow: hidden;
  }
  .card-front { left: 81px; background: var(--ink-black); }
  .card-back { left: 602px; background: var(--maroon); }

  .brand-name {
    font-family: "Roboto Slab", Georgia, serif;
    font-weight: 700;
    color: var(--cream);
    text-transform: uppercase;
    letter-spacing: 1px;
    text-align: center;
    line-height: 1.15;
  }
  .card-front .brand-name {
    position: absolute;
    left: 0; right: 0; top: 78px;
    font-size: 36px;
  }
  .service-band {
    position: absolute;
    left: 0; right: 0; top: 247px;
    height: 27px;
    background: var(--maroon);
    color: var(--cream);
    font-size: 12px;
    line-height: 27px;
    text-align: center;
  }

  .holder-name {
    position: absolute;
    left: 24px; top: 32px;
    font-family: "Roboto Slab", Georgia, serif;
    font-weight: 700;
    font-size: 19px;
    color: var(--gold);
  }
  .holder-title {
    position: absolute;
    left: 24px; top: 59px;
    font-size: 10.5px;
    color: var(--white);
  }
  .card-back .brand-name {
    position: absolute;
    left: 282px; width: 180px; top: 48px;
    font-size: 24px;
  }
  .contact-list {
    position: absolute;
    left: 24px; top: 160px;
    list-style: none;
  }
  .contact-list li {
    display: flex;
    align-items: center;
    height: 17px;
    font-size: 12px;
    color: var(--white);
  }
  .contact-list svg { width: 12px; height: 12px; margin-right: 11px; fill: var(--gold); flex: none; }
  .wave { position: absolute; left: 0; top: 0; width: 485px; height: 294px; }
  .service-list {
    position: absolute;
    right: 20px; top: 215px;
    list-style: none;
    text-align: right;
    color: var(--maroon-deep);
    font-weight: 500;
    font-size: 12px;
    line-height: 16px;
  }
  .service-list .chev { display: inline-block; width: 20px; text-align: right; }
  .service-list .pad { display: inline-block; width: 20px; }
</style>
</head>
<body>
  <section class="card card-front">
    <div class="brand-name">Quillmoor<br>Air</div>
    <div class="service-band">Residential &amp; Light Commercial Heating &nbsp;• Air Conditioning Contractor</div>
  </section>

  <section class="card card-back">
    <svg class="wave" viewBox="0 0 485 294" aria-hidden="true">
      <path d="M0 246 C120 270 250 250 330 210 C390 182 440 172 485 170 L485 294 L0 294 Z" fill="var(--orange)"/>
      <path d="M0 240 C60 262 160 282 262 278 C180 282 80 270 0 256 Z" fill="var(--wave-red)"/>
      <path d="M30 254 C140 272 240 250 320 205 C380 172 440 160 485 158 L485 166 C440 168 385 180 326 212 C245 258 140 276 30 254 Z" fill="var(--wave-yellow)"/>
    </svg>

    <div class="holder-name">Dominic Westerhall</div>
    <div class="holder-title">Managing Director</div>
    <div class="brand-name">Quillmoor<br>Air</div>

    <ul class="contact-list">
      <li><svg viewBox="0 0 24 24"><path d="M3 8c0-2 2-4 9-4s9 2 9 4v2h-5V8H8v2H3z M6 11h12l2 9H4z"/></svg>862-415-2736</li>
      <li><svg viewBox="0 0 24 24"><path d="M2 5h20v14H2z M2 5l10 8 10-8" stroke="var(--maroon)" stroke-width="1.5"/></svg>info@QuillmoorAirLLC.example</li>
      <li><svg viewBox="0 0 24 24"><path d="M12 2a7 7 0 0 0-7 7c0 5 7 13 7 13s7-8 7-13a7 7 0 0 0-7-7zm0 10a3 3 0 1 1 0-6 3 3 0 0 1 0 6z"/></svg>PO box 518 Brightwater NJ 07912</li>
      <li><svg viewBox="0 0 24 24"><circle cx="12" cy="12" r="10"/><path d="M2 12h20M12 2c-4 5-4 15 0 20M12 2c4 5 4 15 0 20" stroke="var(--maroon)" stroke-width="1.5" fill="none"/></svg>QuillmoorAirLLC.example</li>
    </ul>

    <ul class="service-list">
      <li>Air Conditioning<span class="chev">«</span></li>
      <li>Contractor<span class="pad"></span></li>
      <li>Residential and Light<span class="chev">«</span></li>
      <li>Commercial Heating<span class="pad"></span></li>
    </ul>
  </section>
</body>
</html>
```